Flyer-Design für Hundephysiopraxis
Zielgruppe
Ich bin selbstständige Hundephysiotherapeutin / Hundeosteopathin /Hundefitnesstrainerin. Meine Zielgruppe sind Hundehalter bzw. allgemein Tierhalter (biete noch weitere Dinge für Hunde/Tiere an) aber auch Tierärzte.
Aufgabenstellung
Es wäre schön, wenn Sie die Texte ähnlich wie auf meiner Homepage gestalten (z.B. Infos aus der Startseite oder Therapieformen).
Prinzipiell sollte es eher natürlich, freundlich und nett gestaltet sein. Schlichtere Farben passend zum Logo.
Homepage: www.pfotenruhe-mitte.de
Bei den Maßen bin ich offen, hatte aber eher an diesen 'typischen Flyer' gedacht (3 seitiger Flyer mit Vorder und Rückseite) bin aber prinzipiell offen :)
Einen Beispiel Flyer habe ich drangehängt sowie z.B. schon ein paar Fotos die man ggf nutzen kann. Weitere Behandlunsfotos kann ich gerne nachreichen.
Die Flyer sollen hauptsächlich bei z.B. Tierärzten / Tierklinik / Tiernahrungsmärkte wie Kornbeutel ausgelegt werden damit Menschen die mich noch nicht kennen auf meine Arbeit aufmerksam werden.

```html
<!DOCTYPE html>
<html lang="de">
<head>
<meta charset="utf-8">
<title>Hundephysiotherapie – Flyer Innenseite</title>
<link rel="stylesheet" href="https://fonts.googleapis.com/css2?family=Dancing+Script:wght@500;600&family=Crimson+Pro:wght@400;600;700&family=Carlito&display=swap">
<style>
  :root {
    --paper: #ffffff;
    --ink: #1d1d1b;
    --heading-blue: #3a6fb7;
    --service-purple: #5f3a8e;
    --sun: #fbe6c4;
    --band-orange: #f0900f;
    --band-yellow: #fcc200;
    --dog-teal: #16a2b8;
    --runner-violet: #a77cc4;
    --dot-lilac: #e4dceb;
  }
  * { margin: 0; padding: 0; box-sizing: border-box; }
  html, body { width: 1200px; height: 848px; overflow: hidden; background: var(--paper); }
  .spread {
    position: relative; width: 1200px; height: 848px; overflow: hidden;
    background: var(--paper); color: var(--ink);
    font-family: "Crimson Pro", "Times New Roman", serif;
  }
  .decor { position: absolute; z-index: 0; }
  .sun { left: 760px; top: -210px; width: 580px; height: 580px; }
  .bands { left: 0; top: 0; width: 1200px; height: 848px; }
  .dog-figure {
    left: 128px; top: 641px; width: 235px; height: 185px;
    background: var(--dog-teal); border-radius: 48% 52% 40% 45% / 55% 50% 45% 40%;
  }
  .dog-photo {
    left: 410px; top: 482px; width: 268px; height: 273px;
    background: linear-gradient(180deg, #6d6f6a 0%, #8c9a7a 45%, #c6cfb8 75%, rgba(255,255,255,0) 100%);
  }
  .runner-figure {
    left: 1005px; top: 480px; width: 175px; height: 352px;
    background: linear-gradient(200deg, var(--runner-violet) 0%, #cdb3de 80%);
    border-radius: 45% 45% 30% 30% / 18% 18% 12% 12%;
    opacity: .85;
  }
  .dot { left: 831px; top: 655px; width: 21px; height: 21px; border-radius: 50%; background: var(--dot-lilac); }

  .panel { position: absolute; top: 0; z-index: 1; }
  .panel-intro { left: 17px; width: 372px; }
  .panel-services { left: 410px; width: 380px; }
  .panel-leech { left: 820px; width: 360px; }

  .panel-title {
    font-family: "Dancing Script", cursive; font-weight: 500;
    color: var(--heading-blue); font-size: 25px; line-height: 30px;
    text-align: center;
  }
  .panel-intro .panel-title { margin-top: 70px; }
  .panel-services .panel-title { margin-top: 70px; }
  .panel-leech .panel-title { margin-top: 72px; }

  .body-text { font-size: 16.4px; line-height: 20.5px; text-align: justify; hyphens: auto; }
  .panel-intro .body-text { margin-left: 0; width: 354px; }
  .panel-intro .body-text p + p { margin-top: 20px; }
  .intro-lead { margin-top: 12px; }
  .signature {
    font-family: "Dancing Script", cursive; color: var(--heading-blue);
    font-size: 14px; margin: 22px 0 0 0;
  }

  .services-label { font-weight: 700; font-size: 17px; margin: 14px 0 0 20px; }
  .service-list {
    list-style: none; margin: 20px 0 0 20px;
    color: var(--service-purple); font-size: 16px; line-height: 20.5px;
  }

  .panel-leech .body-text { margin-top: 34px; width: 356px; }
  .panel-leech .body-text p + p { margin-top: 20px; }
  .uses-label { font-family: "Carlito", "Calibri", sans-serif; font-weight: 400; font-size: 19px; margin-top: 20px; }
  .uses-list { list-style: none; font-size: 16px; line-height: 20.5px; margin-top: 14px; }
</style>
</head>
<body>
<main class="spread">
  <svg class="decor sun" viewBox="0 0 580 580" role="img" aria-label="Helle Sonne mit Strahlen als Hintergrundschmuck">
    <circle cx="290" cy="290" r="290" fill="var(--sun)" opacity=".55"/>
  </svg>

  <svg class="decor bands" viewBox="0 0 1200 848" aria-hidden="true">
    <path d="M0 745 C 200 700 420 690 640 705 C 860 720 1020 760 1200 770 L1200 848 L0 848 Z" fill="var(--band-orange)"/>
    <path d="M0 770 C 220 725 430 715 650 735 C 860 752 1030 790 1200 795 L1200 848 L0 848 Z" fill="var(--band-yellow)"/>
  </svg>

  <div class="decor dog-photo" role="img" aria-label="Foto eines schwarz-weißen Spaniels auf einer Wiese"></div>
  <div class="decor dog-figure" role="img" aria-label="Türkise Silhouette eines springenden Hundes"></div>
  <div class="decor runner-figure" role="img" aria-label="Violette Silhouette einer laufenden Frau"></div>
  <div class="decor dot"></div>

  <section class="panel panel-intro">
    <h2 class="panel-title">Leben ist Bewegung und Bewegung ist Lebensqualität!</h2>
    <div class="body-text">
      <p class="intro-lead">Rennen, laufen, springen, toben und spielen zeigt die Lebensfreude unserer Hunde! Wer keine Schmerzen hat, kann sich frei bewegen und hat Spaß dabei. Wenn unsere Hunde jedoch erkranken oder alt werden, dann benötigen sie unsere Unterstützung.</p>
      <p>Nach einem Unfall, bei Schmerzen oder Beschwerden im Rücken und in den Gelenken, nach Operationen oder bei Lahmheiten können Physiotherapie sowie Osteopathie helfen. Es lindert die Schmerzen, lockert verspannte Muskulatur, verbessert die Beweglichkeit oder stellt diese wiederher. Weiterhin baut Physiotherapie Muskulatur auf, fördert die Genesung und hilft im Alter fit zu bleiben.</p>
      <p>Ich helfe Deinem Hund gerne dabei, die Gesundheit und damit die Lebensqualität und Lebensfreude zurück zu erhalten.</p>
    </div>
    <p class="signature">– Marlene Hoffbauer</p>
  </section>

  <section class="panel panel-services">
    <h2 class="panel-title">Für mich steht Dein Hund an erster Stelle. Therapie mit Herz.</h2>
    <p class="services-label">Leistung:</p>
    <ul class="service-list">
      <li>Hundephysiotherapie</li>
      <li>Hundeosteopathie (i.A.)</li>
      <li>Breuß-Massage</li>
      <li>Dorn-Therapie</li>
      <li>Hundefitnesstrainer (i.A.)</li>
      <li>Blutegeltherapie</li>
      <li>Bachblütenberatung (siehe Rückseite)</li>
      <li>Tierkommunikation</li>
      <li>Edelsteintherapie</li>
      <li>Mykotherapie</li>
    </ul>
  </section>

  <section class="panel panel-leech">
    <h2 class="panel-title">Blutegeltherapie</h2>
    <div class="body-text">
      <p>Blutegel gehören zu der Unterklasse der Egel (Hirudinea) und werden in der Medizin schon lange zur Behandlung verschiedener Krankheiten eingesetzt.</p>
      <p>Sie haben einen Saugnapf, mit dem sie sich an die zu behandelnden Stellen festsetzen und Blut saugen. Das Speichel-Sekret des Blutegels, welches beim Beissen in die Wunde des Tieres gelangt, wirkt entzündungs- und gerinnungshemmend, schmerzlindernd und regt den Lymphfluss an.</p>
    </div>
    <h3 class="uses-label">Einsatzgebiete</h3>
    <ul class="uses-list">
      <li>Arthrosen</li>
      <li>Arthritis</li>
      <li>Gelenkentzündungen</li>
      <li>Hauterkrankungen</li>
      <li>Nervenentzündungen</li>
      <li>Sehnenentzündungen</li>
      <li>Sehnenschäden</li>
      <li>Durchblutungsstörungen</li>
    </ul>
  </section>
</main>
</body>
</html>
```